KLR Buildworks - Civil Construction Construction Company (Telecommunications)

Need a basic website to refine our branding to a current reflection of our service offerings. KLR Buildworks provides civil construction services specializing in telecommunication sector.
I have started to create a website using word press. I would like to have someone refine the design and polish the overall look and functionality of the site. I would like to website to function in the wordpress format to allow for future edits and control of site.
Included site preview:
https://pvhosts-ua.pagemakerbench.example/7e2d94fa.com/Admin/index.html/qm_draft_view

```html
<!DOCTYPE html>
<html lang="en">
<head>
<meta charset="utf-8">
<title>KLR Buildworks – Homepage, light and dark</title>
<link rel="stylesheet" href="https://fonts.googleapis.com/css2?family=Rajdhani:wght@600;700&family=Raleway:wght@400;500;600&display=swap">
<style>
:root{
  --red:#e3111b;
  --stage:#1c1c1c;
  --paper:#ffffff;
  --ink:#111111;
  --body:#333333;
  --header:#ffffff;
  --band:#ececec;
  --lead:#111111;
  --big-mark:rgba(0,0,0,.06);
  --footer-mark:#0a0a0a;
  --dark:#141619;
}
*{box-sizing:border-box}
html,body{margin:0;width:762px;height:1200px;overflow:hidden;background:var(--stage)}
.page{position:absolute;top:21px;width:351px;height:1162px;overflow:hidden;background:var(--paper);color:var(--ink);font-family:Raleway,sans-serif}
.page--light{left:22px}
.page--dark{left:391px;--paper:#000;--ink:#fff;--body:#e2e2e2;--header:#000;--band:#0b0b0b;--lead:var(--red);--big-mark:rgba(255,255,255,.05);--footer-mark:#fff}
.page *{position:absolute;margin:0}
.page svg *{position:static}
.head{font-family:Rajdhani,sans-serif;font-weight:700;text-transform:uppercase}

/* header */
.site-header{left:0;top:0;width:351px;height:23px;background:var(--header)}
.brand{left:18px;top:5px;font-family:Rajdhani,sans-serif;font-weight:700;font-size:9px;letter-spacing:.2px;color:var(--ink);white-space:nowrap}
.nav-link{top:9px;font-family:Rajdhani,sans-serif;font-weight:600;font-size:3.6px;color:var(--ink);white-space:nowrap}
.search-icon{left:272px;top:8.5px}
.call-btn{left:285px;top:5px;width:53px;height:13px;background:var(--red);color:#fff;font-family:Rajdhani,sans-serif;font-weight:700;font-size:5px;line-height:13px;text-align:center}

/* hero */
.hero-photo{left:0;top:23px;width:351px;height:190px;background:linear-gradient(160deg,#3e5335 0%,#2b3a27 30%,#6b2520 55%,#8a2b22 65%,#4d4a3f 85%,#3a3a33 100%)}
.hero-shade{left:64px;top:62px;width:226px;height:80px;background:rgba(20,22,20,.35)}
.hero-title{left:0;top:78px;width:351px;text-align:center;color:#fff;font-size:18.5px;line-height:20px;letter-spacing:.4px}
.hero-copy{left:75px;top:116px;width:201px;text-align:center;color:#fff;font-size:3.7px;line-height:7px}
.btn{background:var(--red);color:#fff;font-family:Rajdhani,sans-serif;font-weight:700;font-size:5px;text-align:center;text-transform:uppercase}
.hero-btn{left:149px;top:143px;width:53px;height:12px;line-height:12px}
.hero-dots{left:168px;top:179px}
.hero-edge{left:0;top:170px}

/* section titles */
.sec-title{left:0;width:351px;text-align:center;font-size:8.5px;color:var(--ink)}
.sec-title::after{content:"";position:absolute;left:160px;top:10px;width:32px;height:2.2px;background:var(--red);clip-path:polygon(0 0,100% 0,60% 100%,0 30%)}
.sec-title--on-dark{color:#fff}
.sec-title--on-dark::after{background:#fff}
.sec-copy{text-align:center;color:var(--body);font-size:3.6px;line-height:7.5px}

/* profile */
.profile-mark{left:80px;top:230px;width:200px;text-align:center;font-family:Rajdhani,sans-serif;font-weight:700;font-size:56px;line-height:56px;color:var(--big-mark)}
.profile-lead{left:20px;top:243px;width:311px;text-align:center;font-family:Rajdhani,sans-serif;font-weight:600;font-size:4px;color:var(--lead);text-transform:uppercase}
.profile-copy{left:48px;top:252px;width:255px}
.profile-scope{left:20px;top:317px;width:311px;text-align:center;font-family:Rajdhani,sans-serif;font-weight:600;font-size:4px;color:var(--ink);text-transform:uppercase}
.service-photo{top:330px;width:66px;height:73px}
.service-name{top:407px;width:66px;text-align:center;font-family:Rajdhani,sans-serif;font-weight:700;font-size:3.9px;line-height:7.5px;color:var(--ink);text-transform:uppercase}
.service-name--accent{color:var(--red)}
.profile-edge{left:0;top:428px}

/* why choose us */
.why-band{left:0;top:452px;width:351px;height:200px;background:linear-gradient(120deg,#2a1c1c 0%,#3a2422 25%,#1f2226 55%,#2b2e33 80%,#1a1c1f 100%)}
.why-shade{left:0;top:452px;width:351px;height:200px;background:rgba(15,18,22,.45)}
.why-panel{top:522px;width:86px;height:79px;background:rgba(40,42,46,.55)}
.why-panel--accent{background:rgba(227,17,27,.6)}
.why-icon{top:510px}
.why-name{top:553px;width:100px;text-align:center;color:#fff;font-size:5px}
.why-copy{top:563px;width:100px;text-align:center;color:#f0f0f0;font-size:3.6px;line-height:8.2px}
.why-edge{left:0;top:622px}

/* our work */
.work-copy{left:48px;top:688px;width:255px}
.work-photo{position:absolute}

/* contact */
.contact-band{left:0;top:847px;width:351px;height:190px;background:var(--band)}
.field{background:#fff;border:.5px solid #9a9a9a;color:#555;font-size:3.4px;padding:5.5px 3px 0}
.send-btn{left:149px;top:969px;width:53px;height:13px;line-height:13px}

/* footer */
.footer-band{left:0;top:990px;width:351px;height:172px;background:linear-gradient(180deg,#1d2024 0%,#1a1c20 60%,#111315 100%)}
.footer-edge{left:0;top:990px}
.footer-mark{left:4px;top:988px;font-family:Rajdhani,sans-serif;font-weight:700;font-size:44px;line-height:44px;color:var(--footer-mark);letter-spacing:1px}
.mail-title{left:0;top:1033px;width:351px;text-align:center;color:#fff;font-size:8.5px}
.mail-box{left:88px;top:1050px;width:175px;height:14px;background:#fff;border:1px solid var(--red);border-radius:2px}
.mail-hint{left:12px;top:4px;font-size:3.6px;color:#aaa}
.mail-btn{left:131px;top:1px;width:41px;height:10px;line-height:10px;border-radius:1px;font-size:4px}
.rule{left:21px;width:309px;height:.5px;background:rgba(255,255,255,.35)}
.foot-brand{left:39px;top:1091px;font-family:Rajdhani,sans-serif;font-weight:700;font-size:8.5px;color:#fff;white-space:nowrap}
.social{top:1110px;width:8.5px;height:8.5px;border-radius:50%;background:var(--red);border:.6px solid #fff}
.foot-head{top:1085px;font-family:Rajdhani,sans-serif;font-weight:700;font-size:4.2px;color:#fff;text-transform:uppercase}
.foot-list{top:1093px;list-style:none;padding:0;color:#e6e6e6;font-size:3.5px;line-height:8.2px}
.foot-list li{position:relative}
.foot-list li::before{content:"» ";}
.foot-contact{top:1093px;color:#e6e6e6;font-size:3.5px;line-height:7.5px}
.copyright{left:0;top:1143px;width:351px;text-align:center;color:#e6e6e6;font-size:3.4px}
.copyright b{position:static;color:var(--red);font-weight:500}
</style>
</head>
<body>

<!-- ===================== LIGHT THEME ===================== -->
<main class="page page--light">
  <header class="site-header">
    <p class="brand">KLR BUILDWORKS</p>
    <span class="nav-link" style="left:123px">HOME</span>
    <span class="nav-link" style="left:149px">ABOUT</span>
    <span class="nav-link" style="left:170px">WHY CHOOSE US</span>
    <span class="nav-link" style="left:211px">OUR WORK</span>
    <span class="nav-link" style="left:243px">CONTACT US</span>
    <svg class="search-icon" width="5" height="5" viewBox="0 0 10 10"><circle cx="4" cy="4" r="3" fill="none" stroke="currentColor" stroke-width="1.6"/><line x1="6.3" y1="6.3" x2="9" y2="9" stroke="currentColor" stroke-width="1.6"/></svg>
    <p class="call-btn">1 (780) 555-0148</p>
  </header>

  <div class="hero-photo" role="img" aria-label="Red tracked trenching machine laying cable beside a forest rail line"></div>
  <div class="hero-shade"></div>
  <h1 class="hero-title head">Welcome to<br>KLR Buildworks</h1>
  <p class="hero-copy">KLR Buildworks is a safety conscious, productive and efficient construction firm capable of all facets of civil construction. We have completed thousands of projects across Alberta, Saskatchewan and British Columbia.</p>
  <p class="btn hero-btn">Get Started</p>
  <svg class="hero-dots" width="16" height="4" viewBox="0 0 16 4"><circle cx="2" cy="2" r="1.4" fill="#e3111b"/><circle cx="6" cy="2" r="1.4" fill="#fff"/><circle cx="10" cy="2" r="1.4" fill="#fff"/><circle cx="14" cy="2" r="1.4" fill="#fff"/></svg>
  <svg class="hero-edge" width="351" height="44" viewBox="0 0 351 44"><polygon points="0,38 351,27 351,44 0,44" fill="#fff"/><polygon points="175,32 351,6 351,27" fill="#e3111b"/></svg>

  <p class="profile-mark">KLR</p>
  <h2 class="sec-title head" style="top:223px">Company Profile</h2>
  <p class="profile-lead">At KLR Buildworks we strive to provide creative solutions, on-time, on-budget and beyond expectations</p>
  <p class="sec-copy profile-copy">Each of KLR's construction crews are dispatched with a full complement of late model equipment and tools required to complete civil underground construction projects in a safe and efficient manner meeting all criteria established by client, governing bodies and site environments. We constantly maintain and update our fleet to supply our clients with the most effective and modern construction solutions possible. Our dedicated maintenance team ensures we are compliant across our wide areas of operation. All this achieved without compromising safety or quality. We understand the unique challenges of deploying crews and completing civil construction projects within Western Canada's diverse geography, terrain and climate. Our experience helps us achieve success in some of the most challenging situations and conditions. Safety is a top priority, closely tied to our day-to-day operations. We believe that effective implementation of Health, Safety and Environmental plans are critical to the success of any project, no matter the size or scope.</p>
  <p class="profile-scope">KLR Buildworks is capable of providing full turnkey project execution, including:</p>
  <div class="service-photo" style="left:39px;background:linear-gradient(160deg,#5b6170,#2f3440 60%,#c9842a)" role="img" aria-label="Project managers reviewing plans on site"></div>
  <div class="service-photo" style="left:108px;background:linear-gradient(170deg,#8a94a8,#47505f 50%,#b4271f)" role="img" aria-label="Worker in hard hat and safety gear"></div>
  <div class="service-photo" style="left:177.5px;background:linear-gradient(180deg,#9aa2a0,#d3d6d2 50%,#5e6b4e)" role="img" aria-label="Vacuum excavation truck on a roadside"></div>
  <div class="service-photo" style="left:247px;background:linear-gradient(160deg,#3d4047,#6e6a5a 45%,#b7c23a)" role="img" aria-label="Inspector with laptop checking quality on site"></div>
  <p class="service-name" style="left:39px">Project design and<br>management</p>
  <p class="service-name service-name--accent" style="left:108px">Health, safety and<br>environmental management</p>
  <p class="service-name" style="left:177.5px">Material procurement<br>and management</p>
  <p class="service-name" style="left:247px">Quality assurance<br>management</p>
  <svg class="profile-edge" width="351" height="25" viewBox="0 0 351 25"><polygon points="0,0 0,24 185,24" fill="#e3111b"/></svg>

  <div class="why-band" role="img" aria-label="Cable reel and tracked machine at a work yard"></div>
  <div class="why-shade"></div>
  <h2 class="sec-title sec-title--on-dark head" style="top:474px">Why Choose Us</h2>
  <div class="why-panel" style="left:39px"></div>
  <div class="why-panel why-panel--accent" style="left:132px"></div>
  <div class="why-panel" style="left:226px"></div>
  <svg class="why-icon" style="left:64px" width="36" height="36" viewBox="0 0 36 36"><rect x="8" y="8" width="20" height="20" transform="rotate(45 18 18)" fill="#e3111b" stroke="#fff" stroke-width=".8"/><path d="M18 11l6 2.5v4.5c0 4-3 6.5-6 7.5-3-1-6-3.5-6-7.5v-4.5z" fill="none" stroke="#fff" stroke-width="1"/><path d="M15 18l2 2 4-4" fill="none" stroke="#fff" stroke-width="1"/></svg>
  <svg class="why-icon" style="left:157.5px" width="36" height="36" viewBox="0 0 36 36"><rect x="8" y="8" width="20" height="20" transform="rotate(45 18 18)" fill="#e3111b" stroke="#fff" stroke-width=".8"/><circle cx="18" cy="18" r="6" fill="none" stroke="#fff" stroke-width="1"/><path d="M18 14.5V18l2.5 1.5" fill="none" stroke="#fff" stroke-width="1"/></svg>
  <svg class="why-icon" style="left:251px" width="36" height="36" viewBox="0 0 36 36"><rect x="8" y="8" width="20" height="20" transform="rotate(45 18 18)" fill="#e3111b" stroke="#fff" stroke-width=".8"/><path d="M11 17l4-3 3 2 3-2 4 3M14 18l3 3 2-1 2 1 3-3" fill="none" stroke="#fff" stroke-width="1"/></svg>
  <h3 class="why-name head" style="left:32px">Safety Excellence</h3>
  <h3 class="why-name head" style="left:125.5px">Efficient Crews</h3>
  <h3 class="why-name head" style="left:219px">Reliable Services</h3>
  <p class="why-copy" style="left:32px">Accredited health and safety program<br>Proven track record of safety excellence<br>Continuous training and development of employees</p>
  <p class="why-copy" style="left:125.5px">Productive and efficient crews<br>Current fleet of modern equipment<br>Use of latest construction techniques/technologies</p>
  <p class="why-copy" style="left:219px">Quality and process driven<br>Excellent customer service<br>Privately owned and operated<br>Dependable, Reliable and Honest</p>
  <svg class="why-edge" width="351" height="32" viewBox="0 0 351 32"><polygon points="0,26 180,28 351,31 351,32 0,32" fill="#fff"/><polygon points="180,28 351,3 351,31" fill="#e3111b"/></svg>

  <h2 class="sec-title head" style="top:672px">Our Work</h2>
  <p class="sec-copy work-copy">KLR Buildworks is equipped to complete civil construction projects of all sizes and complexities. From small alterations and repairs to large scale network deployments throughout large geographical areas.</p>
  <div class="work-photo" style="left:39.5px;top:710.5px;width:134px;height:108.5px;background:linear-gradient(150deg,#e7e9ea,#7b2520 40%,#3b3a36 75%,#5e7345)" role="img" aria-label="Crew member servicing a red trenching machine"></div>
  <div class="work-photo" style="left:177px;top:710.5px;width:66.5px;height:52.5px;background:linear-gradient(180deg,#b9c6d4,#56683e 55%,#2e2e2c)" role="img" aria-label="Machine operator in a residential street"></div>
  <div class="work-photo" style="left:245.5px;top:710.5px;width:66px;height:52.5px;background:linear-gradient(150deg,#3b8fb8,#6c6a63 55%,#a3272a)" role="img" aria-label="Close-up of blue drilling equipment"></div>
  <div class="work-photo" style="left:177px;top:766.5px;width:66.5px;height:52.5px;background:linear-gradient(170deg,#7f8c9b,#c9a72a 55%,#3c3b36)" role="img" aria-label="Yellow excavator on a job site"></div>
  <div class="work-photo" style="left:245.5px;top:766.5px;width:66px;height:52.5px;background:linear-gradient(180deg,#cfd6de,#5b7040 55%,#2a2a28)" role="img" aria-label="Directional drill rig on grass"></div>

  <div class="contact-band"></div>
  <h2 class="sec-title head" style="top:874px">Contact Us</h2>
  <p class="field" style="left:68px;top:895px;width:105px;height:14px">First Name</p>
  <p class="field" style="left:177.5px;top:895px;width:105px;height:14px">Last Name</p>
  <p class="field" style="left:68px;top:913px;width:105px;height:14px">Email</p>
  <p class="field" style="left:177.5px;top:913px;width:105px;height:14px">Phone</p>
  <p class="field" style="left:68px;top:932px;width:214.5px;height:29px">How Can We Help?</p>
  <p class="btn send-btn">Submit</p>

  <div class="footer-band" role="img" aria-label="Dimmed crew trucks at a work site"></div>
  <svg class="footer-edge" width="351" height="40" viewBox="0 0 351 40"><polygon points="0,0 351,0 351,10 0,35" fill="#ececec"/><polygon points="0,30 351,8 351,10 0,37" fill="#e3111b"/></svg>
  <p class="footer-mark">KLR</p>
  <h2 class="mail-title head">Join Our Mailing List</h2>
  <div class="mail-box"><span class="mail-hint">Enter Email Here</span><span class="btn mail-btn">Subscribe</span></div>
  <div class="rule" style="top:1075px"></div>
  <p class="foot-brand">KLR BUILDWORKS</p>
  <span class="social" style="left:56px" aria-label="Social profile"></span>
  <span class="social" style="left:69px" aria-label="Social profile"></span>
  <span class="social" style="left:82px" aria-label="Social profile"></span>
  <span class="social" style="left:95px" aria-label="Social profile"></span>
  <p class="foot-head" style="left:134.5px">Quick Links</p>
  <ul class="foot-list" style="left:134.5px"><li>Home</li><li>About</li><li>Why choose us</li><li>our work</li><li>Contact Us</li></ul>
  <p class="foot-head" style="left:186.5px">Legal</p>
  <ul class="foot-list" style="left:186.5px"><li>Privacy Policy</li><li>Terms &amp; Conditions</li><li>Contact Us</li><li>Cookie Policy</li></ul>
  <p class="foot-head" style="left:248px">Contact Us</p>
  <p class="foot-contact" style="left:246px">⌖ 218 Ridgeline Rd Stony Plain,<br>&nbsp;&nbsp;&nbsp;AB T7Z 1K4 Canada<br>☎ 1 (780) 555-0148<br><br>✉ info@klrbuildworks.example</p>
  <div class="rule" style="top:1136px"></div>
  <p class="copyright">© Copyright 2021 <b>KLR BUILDWORKS</b> &nbsp;|&nbsp; All Rights Reserved</p>
</main>

<!-- ===================== DARK THEME ===================== -->
<main class="page page--dark">
  <header class="site-header">
    <p class="brand">KLR BUILDWORKS</p>
    <span class="nav-link" style="left:123px">HOME</span>
    <span class="nav-link" style="left:149px">ABOUT</span>
    <span class="nav-link" style="left:170px">WHY CHOOSE US</span>
    <span class="nav-link" style="left:211px">OUR WORK</span>
    <span class="nav-link" style="left:243px">CONTACT US</span>
    <svg class="search-icon" width="5" height="5" viewBox="0 0 10 10" style="color:#fff"><circle cx="4" cy="4" r="3" fill="none" stroke="currentColor" stroke-width="1.6"/><line x1="6.3" y1="6.3" x2="9" y2="9" stroke="currentColor" stroke-width="1.6"/></svg>
    <p class="call-btn">1 (780) 555-0148</p>
  </header>

  <div class="hero-photo" role="img" aria-label="Red tracked trenching machine laying cable beside a forest rail line"></div>
  <div class="hero-shade"></div>
  <h1 class="hero-title head">Welcome to<br>KLR Buildworks</h1>
  <p class="hero-copy">KLR Buildworks is a safety conscious, productive and efficient construction firm capable of all facets of civil construction. We have completed thousands of projects across Alberta, Saskatchewan and British Columbia.</p>
  <p class="btn hero-btn">Get Started</p>
  <svg class="hero-dots" width="16" height="4" viewBox="0 0 16 4"><circle cx="2" cy="2" r="1.4" fill="#e3111b"/><circle cx="6" cy="2" r="1.4" fill="#fff"/><circle cx="10" cy="2" r="1.4" fill="#fff"/><circle cx="14" cy="2" r="1.4" fill="#fff"/></svg>
  <svg class="hero-edge" width="351" height="44" viewBox="0 0 351 44"><polygon points="0,38 351,27 351,44 0,44" fill="#000"/><polygon points="175,32 351,6 351,27" fill="#e3111b"/></svg>

  <p class="profile-mark">KLR</p>
  <h2 class="sec-title head" style="top:223px">Company Profile</h2>
  <p class="profile-lead">At KLR Buildworks we strive to provide creative solutions, on-time, on-budget and beyond expectations</p>
  <p class="sec-copy profile-copy">Each of KLR's construction crews are dispatched with a full complement of late model equipment and tools required to complete civil underground construction projects in a safe and efficient manner meeting all criteria established by client, governing bodies and site environments. We constantly maintain and update our fleet to supply our clients with the most effective and modern construction solutions possible. Our dedicated maintenance team ensures we are compliant across our wide areas of operation. All this achieved without compromising safety or quality. We understand the unique challenges of deploying crews and completing civil construction projects within Western Canada's diverse geography, terrain and climate. Our experience helps us achieve success in some of the most challenging situations and conditions. Safety is a top priority, closely tied to our day-to-day operations. We believe that effective implementation of Health, Safety and Environmental plans are critical to the success of any project, no matter the size or scope.</p>
  <p class="profile-scope">KLR Buildworks is capable of providing full turnkey project execution, including:</p>
  <div class="service-photo" style="left:39px;background:linear-gradient(160deg,#5b6170,#2f3440 60%,#c9842a)" role="img" aria-label="Project managers reviewing plans on site"></div>
  <div class="service-photo" style="left:108px;background:linear-gradient(170deg,#8a94a8,#47505f 50%,#b4271f)" role="img" aria-label="Worker in hard hat and safety gear"></div>
  <div class="service-photo" style="left:177.5px;background:linear-gradient(180deg,#9aa2a0,#d3d6d2 50%,#5e6b4e)" role="img" aria-label="Vacuum excavation truck on a roadside"></div>
  <div class="service-photo" style="left:247px;background:linear-gradient(160deg,#3d4047,#6e6a5a 45%,#b7c23a)" role="img" aria-label="Inspector with laptop checking quality on site"></div>
  <p class="service-name" style="left:39px">Project design and<br>management</p>
  <p class="service-name service-name--accent" style="left:108px">Health, safety and<br>environmental management</p>
  <p class="service-name" style="left:177.5px">Material procurement<br>and management</p>
  <p class="service-name" style="left:247px">Quality assurance<br>management</p>
  <svg class="profile-edge" width="351" height="25" viewBox="0 0 351 25"><polygon points="0,0 0,24 185,24" fill="#e3111b"/></svg>

  <div class="why-band" role="img" aria-label="Cable reel and tracked machine at a work yard"></div>
  <div class="why-shade"></div>
  <h2 class="sec-title sec-title--on-dark head" style="top:474px">Why Choose Us</h2>
  <div class="why-panel" style="left:39px"></div>
  <div class="why-panel why-panel--accent" style="left:132px"></div>
  <div class="why-panel" style="left:226px"></div>
  <svg class="why-icon" style="left:64px" width="36" height="36" viewBox="0 0 36 36"><rect x="8" y="8" width="20" height="20" transform="rotate(45 18 18)" fill="#e3111b" stroke="#fff" stroke-width=".8"/><path d="M18 11l6 2.5v4.5c0 4-3 6.5-6 7.5-3-1-6-3.5-6-7.5v-4.5z" fill="none" stroke="#fff" stroke-width="1"/><path d="M15 18l2 2 4-4" fill="none" stroke="#fff" stroke-width="1"/></svg>
  <svg class="why-icon" style="left:157.5px" width="36" height="36" viewBox="0 0 36 36"><rect x="8" y="8" width="20" height="20" transform="rotate(45 18 18)" fill="#e3111b" stroke="#fff" stroke-width=".8"/><circle cx="18" cy="18" r="6" fill="none" stroke="#fff" stroke-width="1"/><path d="M18 14.5V18l2.5 1.5" fill="none" stroke="#fff" stroke-width="1"/></svg>
  <svg class="why-icon" style="left:251px" width="36" height="36" viewBox="0 0 36 36"><rect x="8" y="8" width="20" height="20" transform="rotate(45 18 18)" fill="#e3111b" stroke="#fff" stroke-width=".8"/><path d="M11 17l4-3 3 2 3-2 4 3M14 18l3 3 2-1 2 1 3-3" fill="none" stroke="#fff" stroke-width="1"/></svg>
  <h3 class="why-name head" style="left:32px">Safety Excellence</h3>
  <h3 class="why-name head" style="left:125.5px">Efficient Crews</h3>
  <h3 class="why-name head" style="left:219px">Reliable Services</h3>
  <p class="why-copy" style="left:32px">Accredited health and safety program<br>Proven track record of safety excellence<br>Continuous training and development of employees</p>
  <p class="why-copy" style="left:125.5px">Productive and efficient crews<br>Current fleet of modern equipment<br>Use of latest construction techniques/technologies</p>
  <p class="why-copy" style="left:219px">Quality and process driven<br>Excellent customer service<br>Privately owned and operated<br>Dependable, Reliable and Honest</p>
  <svg class="why-edge" width="351" height="32" viewBox="0 0 351 32"><polygon points="0,26 180,28 351,31 351,32 0,32" fill="#000"/><polygon points="180,28 351,3 351,31" fill="#e3111b"/></svg>

  <h2 class="sec-title head" style="top:672px">Our Work</h2>
  <p class="sec-copy work-copy">KLR Buildworks is equipped to complete civil construction projects of all sizes and complexities. From small alterations and repairs to large scale network deployments throughout large geographical areas.</p>
  <div class="work-photo" style="left:39.5px;top:710.5px;width:134px;height:108.5px;background:linear-gradient(150deg,#e7e9ea,#7b2520 40%,#3b3a36 75%,#5e7345)" role="img" aria-label="Crew member servicing a red trenching machine"></div>
  <div class="work-photo" style="left:177px;top:710.5px;width:66.5px;height:52.5px;background:linear-gradient(180deg,#b9c6d4,#56683e 55%,#2e2e2c)" role="img" aria-label="Machine operator in a residential street"></div>
  <div class="work-photo" style="left:245.5px;top:710.5px;width:66px;height:52.5px;background:linear-gradient(150deg,#3b8fb8,#6c6a63 55%,#a3272a)" role="img" aria-label="Close-up of blue drilling equipment"></div>
  <div class="work-photo" style="left:177px;top:766.5px;width:66.5px;height:52.5px;background:linear-gradient(170deg,#7f8c9b,#c9a72a 55%,#3c3b36)" role="img" aria-label="Yellow excavator on a job site"></div>
  <div class="work-photo" style="left:245.5px;top:766.5px;width:66px;height:52.5px;background:linear-gradient(180deg,#cfd6de,#5b7040 55%,#2a2a28)" role="img" aria-label="Directional drill rig on grass"></div>

  <div class="contact-band"></div>
  <h2 class="sec-title head" style="top:874px">Contact Us</h2>
  <p class="field" style="left:68px;top:895px;width:105px;height:14px">First Name</p>
  <p class="field" style="left:177.5px;top:895px;width:105px;height:14px">Last Name</p>
  <p class="field" style="left:68px;top:913px;width:105px;height:14px">Email</p>
  <p class="field" style="left:177.5px;top:913px;width:105px;height:14px">Phone</p>
  <p class="field" style="left:68px;top:932px;width:214.5px;height:29px">How Can We Help?</p>
  <p class="btn send-btn">Submit</p>

  <div class="footer-band" role="img" aria-label="Dimmed crew trucks at a work site"></div>
  <svg class="footer-edge" width="351" height="40" viewBox="0 0 351 40"><polygon points="0,0 351,0 351,10 0,35" fill="#0b0b0b"/><polygon points="0,30 351,8 351,10 0,37" fill="#e3111b"/></svg>
  <p class="footer-mark">KLR</p>
  <h2 class="mail-title head">Join Our Mailing List</h2>
  <div class="mail-box"><span class="mail-hint">Enter Email Here</span><span class="btn mail-btn">Subscribe</span></div>
  <div class="rule" style="top:1075px"></div>
  <p class="foot-brand">KLR BUILDWORKS</p>
  <span class="social" style="left:56px" aria-label="Social profile"></span>
  <span class="social" style="left:69px" aria-label="Social profile"></span>
  <span class="social" style="left:82px" aria-label="Social profile"></span>
  <span class="social" style="left:95px" aria-label="Social profile"></span>
  <p class="foot-head" style="left:134.5px">Quick Links</p>
  <ul class="foot-list" style="left:134.5px"><li>Home</li><li>About</li><li>Why choose us</li><li>our work</li><li>Contact Us</li></ul>
  <p class="foot-head" style="left:186.5px">Legal</p>
  <ul class="foot-list" style="left:186.5px"><li>Privacy Policy</li><li>Terms &amp; Conditions</li><li>Contact Us</li><li>Cookie Policy</li></ul>
  <p class="foot-head" style="left:248px">Contact Us</p>
  <p class="foot-contact" style="left:246px">⌖ 218 Ridgeline Rd Stony Plain,<br>&nbsp;&nbsp;&nbsp;AB T7Z 1K4 Canada<br>☎ 1 (780) 555-0148<br><br>✉ info@klrbuildworks.example</p>
  <div class="rule" style="top:1136px"></div>
  <p class="copyright">© Copyright 2021 <b>KLR BUILDWORKS</b> &nbsp;|&nbsp; All Rights Reserved</p>
</main>

</body>
</html>
```